Oil Field Service company needs professional business cards

Looking to clean up our current company business cards and look a little more professional. Brenwick Casing Services is a US based company that services the oil field. We deal with engineers, managers and oil rigs....................................................................................................................................................................................................................................................................................................................................................................................................

Target Market(s)

Oil and Gas professionals

Industry/Entity Type

Oil And Gas

Contact Information for Business Card

See attached photo as example

Font styles to use
Sans Serif

Colors
ec1f27

Requirements
Must have
• Company Logo, Name, Title, Cell, Office, Fax, Email.
• See attached photo
Nice to have
• External CRT, Internal CRT, Casing Crews, Torque Turn, Laydown Machine
Should not have
• Do not introduce any new pictures and keep it professional looking

```html
<!DOCTYPE html>
<html lang="en">
<head>
<meta charset="utf-8">
<title>Brenwick Casing Services – Business Card</title>
<link href="https://fonts.googleapis.com/css2?family=Oswald:wght@300;400&family=Roboto:wght@400;700&display=swap" rel="stylesheet">
<style>
  :root {
    --red: #d9232b;
    --slate: #3d5267;
    --ink: #3a3a3a;
    --card: #f7f7f7;
    --backdrop: #e8e8e8;
  }
  * { margin: 0; padding: 0; box-sizing: border-box; }
  html, body { width: 1200px; height: 576px; overflow: hidden; }
  body { background: var(--backdrop); position: relative; font-family: "Roboto", Arial, sans-serif; }

  .card {
    position: absolute;
    top: 139px;
    width: 484px;
    height: 293px;
    background: var(--card);
    border-radius: 6px;
    overflow: hidden;
    box-shadow: 0 2px 5px rgba(0,0,0,0.18);
  }
  .card--front { left: 82px; }
  .card--back { left: 602px; width: 481px; }

  .brand { text-align: center; color: var(--slate); font-family: "Roboto", Arial, sans-serif; font-weight: 700; }
  .brand__name { display: block; line-height: 1; }
  .brand__tagline { display: block; text-transform: uppercase; }

  .card--front .brand { position: absolute; left: 0; right: 0; top: 84px; }
  .card--front .brand__name { font-size: 54px; letter-spacing: 1px; }
  .card--front .brand__tagline { font-size: 17px; letter-spacing: 3px; margin-top: 14px; }

  .services {
    position: absolute; left: 0; right: 0; top: 220px; height: 26px;
    background: var(--red);
    display: flex; align-items: center; justify-content: center; gap: 7px;
    color: #fff; font-size: 12.5px; font-weight: 700; letter-spacing: 0.2px;
    text-transform: uppercase;
  }
  .services__divider { font-weight: 400; }

  .front-web {
    position: absolute; left: 0; right: 0; top: 262px;
    display: flex; align-items: center; justify-content: center; gap: 10px;
    font-size: 13px; color: var(--ink);
  }
  .front-web__rule { width: 68px; height: 2px; background: var(--red); border-radius: 1px; }

  .edge-band { position: absolute; left: 0; top: 0; bottom: 0; width: 38px; background: var(--red); }
  .edge-rule { position: absolute; left: 38px; top: 0; bottom: 0; width: 6px; background: var(--slate); }

  .card--back .brand { position: absolute; left: 254px; width: 200px; top: 42px; }
  .card--back .brand__name { font-size: 31px; letter-spacing: 0.5px; }
  .card--back .brand__tagline { font-size: 10px; letter-spacing: 2px; margin-top: 10px; }

  .person { position: absolute; left: 66px; top: 158px; }
  .person__name { font-family: "Oswald", Arial, sans-serif; font-weight: 400; font-size: 21px; color: var(--ink); line-height: 1.1; }
  .person__title { font-size: 11px; color: #555; margin-top: 2px; }

  .contacts {
    position: absolute; top: 219px;
    display: flex; flex-direction: column; gap: 3px;
    font-family: "Oswald", Arial, sans-serif; font-weight: 300; font-size: 11.5px; color: var(--ink);
    white-space: nowrap;
  }
  .contacts--phones { left: 68px; }
  .contacts--details { left: 200px; }
  .contact { display: flex; align-items: center; gap: 8px; height: 13px; }
  .contact svg { width: 10px; height: 10px; fill: var(--red); flex: none; }
</style>
</head>
<body>

<section class="card card--front">
  <div class="brand">
    <span class="brand__name">BRENWICK</span>
    <span class="brand__tagline">Casing Services</span>
  </div>
  <div class="services">
    <span>Laydown Machine</span><span class="services__divider">|</span>
    <span>Casing Crew</span><span class="services__divider">|</span>
    <span>Mud Tool</span><span class="services__divider">|</span>
    <span>Torque Turn</span>
  </div>
  <div class="front-web">
    <span class="front-web__rule"></span>
    <span>www.brenwickcs.com</span>
    <span class="front-web__rule"></span>
  </div>
</section>

<section class="card card--back">
  <div class="edge-band"></div>
  <div class="edge-rule"></div>

  <div class="brand">
    <span class="brand__name">BRENWICK</span>
    <span class="brand__tagline">Casing Services</span>
  </div>

  <div class="person">
    <div class="person__name">Carl Whitfield</div>
    <div class="person__title">Area Manager</div>
  </div>

  <div class="contacts contacts--phones">
    <div class="contact">
      <svg viewBox="0 0 10 10" aria-hidden="true"><path d="M2 0.5l2 2-1 1.2c.6 1.3 1.6 2.3 2.9 2.9l1.2-1 2 2-1.3 1.9C4.5 9.3.7 5.5.2 1.8z"/></svg>
      <span>(555) 210-4700</span>
    </div>
    <div class="contact">
      <svg viewBox="0 0 10 10" aria-hidden="true"><path d="M0 9.5h10v-2L8.5 3.5h-7L0 7.5zM3.2 6.4a1.8 1.8 0 1 0 3.6 0a1.8 1.8 0 1 0-3.6 0zM0.3 2.8h9.4v-1.6c-3-1.2-6.4-1.2-9.4 0z"/></svg>
      <span>(555) 318-6492</span>
    </div>
    <div class="contact">
      <svg viewBox="0 0 10 10" aria-hidden="true"><path d="M2.5 0.5h5v2.5h-5zM0.5 3.5h9v4h-2v-1.5h-5v1.5h-2zM3 6.8h4v2.7h-4z"/></svg>
      <span>(555) 210-4231</span>
    </div>
  </div>

  <div class="contacts contacts--details">
    <div class="contact">
      <svg viewBox="0 0 10 10" aria-hidden="true"><path d="M0.5 2h9v6h-9z"/><path d="M0.5 2l4.5 3.5 4.5-3.5" stroke="#f7f7f7" stroke-width="0.8" fill="none"/></svg>
      <span>carlwhitfield@brenwickcs.com</span>
    </div>
    <div class="contact">
      <svg viewBox="0 0 10 10" aria-hidden="true"><circle cx="5" cy="5" r="4.5"/><path d="M0.5 5h9M5 0.5c-2 2.5-2 6.5 0 9M5 0.5c2 2.5 2 6.5 0 9" stroke="#f7f7f7" stroke-width="0.7" fill="none"/></svg>
      <span>www.brenwickcs.com</span>
    </div>
    <div class="contact">
      <svg viewBox="0 0 10 10" aria-hidden="true"><path d="M5 0.3a3.4 3.4 0 0 0-3.4 3.4C1.6 6.2 5 9.8 5 9.8s3.4-3.6 3.4-6.1A3.4 3.4 0 0 0 5 0.3zm0 4.7a1.3 1.3 0 1 1 0-2.6a1.3 1.3 0 0 1 0 2.6z"/></svg>
      <span>Redmesa, OK 73850</span>
    </div>
  </div>
</section>

</body>
</html>
```